Business Card Update, need to bring life to the card, two sided color

We need a new business card design, are moving and changing addresses and need a new look, we have the logos already attached but need a new style moving forward. Can incorporate the color of the logo (The Green) as well, maybe a solid back? We deal with safety products revolving around static electricity and safety lighting. Would like to keep same font in second logo as well.

Target Market(s)

Electrical Safety, Lighting

Contact Information for Business Card

Dale Fenwick
Vice President
Office: 770-555-4821
Cell: 770-555-3067
dale@tkfenwick.example
www.tkfenwick.example
4700 West Harbor Boulevard
Suite #150
Roswell, GA 30076

Font styles to use
Serif
Sans Serif

Requirements
Must have
• Since 1918
Nice to have
• Could use the 100 Year Logo for back of card, would like the back of card to be the same green as logo.
Should not have
• No black cards please.

```html
<!DOCTYPE html>
<html lang="en">
<head>
<meta charset="utf-8">
<title>T.K. Fenwick Business Card</title>
<link rel="stylesheet" href="https://fonts.googleapis.com/css2?family=Arimo:wght@400;700&display=swap">
<style>
:root{
  --green:#0fae73;
  --green-light:#19c287;
  --green-dark:#0a9460;
  --paper:#fbfbfb;
  --swoosh:#cfcfcf;
  --ink:#6d6d6d;
  --backdrop:#e9ebea;
}
*{box-sizing:border-box;margin:0;padding:0}
html,body{width:1200px;height:780px;overflow:hidden}
body{background:var(--backdrop);font-family:"Arimo",Arial,sans-serif;position:relative}
.card{position:absolute;top:235px;width:540px;height:310px;border-radius:22px;overflow:hidden;box-shadow:0 6px 18px rgba(0,0,0,.18)}
.card-front{left:40px;background:var(--paper)}
.card-back{left:620px;background:radial-gradient(circle at 50% 40%,var(--green-light),var(--green) 55%,var(--green-dark))}
.front-shape{position:absolute;inset:0}
.holder{position:absolute;top:14px;right:30px;text-align:right;color:#fff;line-height:1.15}
.holder-name{font-weight:700;font-size:17px;letter-spacing:.5px;text-transform:uppercase}
.holder-title{font-size:12px}
.brand{position:absolute;left:132px;top:118px;display:flex;align-items:center;gap:14px}
.brand-mark{width:72px;height:72px;border-radius:50%;background:var(--green);flex:none}
.brand-name{color:var(--green);font-weight:700;font-size:32px;line-height:1}
.brand-sub{color:var(--green);font-weight:700;font-size:13.5px;margin-top:5px}
.brand-since{color:var(--ink);font-size:11px;margin-top:4px;letter-spacing:1px;text-transform:uppercase}
.rule{position:absolute;left:120px;right:28px;top:220px;height:1px;background:var(--green)}
.contacts{position:absolute;left:84px;right:22px;top:234px;display:flex;justify-content:space-between;font-size:10.5px;color:var(--ink)}
.contact-col{padding-left:10px;border-left:1px solid var(--green);display:flex;flex-direction:column;gap:7px}
.contact-col:first-child{padding-left:0;border-left:none}
.contact-line{display:flex;align-items:center;gap:5px;white-space:nowrap}
.icon{width:11px;height:11px;flex:none}
.back-brand{position:absolute;left:0;right:0;top:96px;display:flex;align-items:center;justify-content:center;gap:16px}
.back-mark{width:86px;height:86px;border-radius:50%;background:#fff;flex:none}
.back-name{color:#fff;font-weight:700;font-size:34px}
.back-web{position:absolute;left:0;right:0;top:222px;text-align:center;color:#fff;font-weight:700;font-size:15px;letter-spacing:.3px}
</style>
</head>
<body>
<section class="card card-front" aria-label="Card front">
  <svg class="front-shape" viewBox="0 0 540 310" aria-hidden="true">
    <path d="M0 0H540V60C330 64 110 120 26 310H0Z" fill="var(--green)"/>
    <path d="M44 310C126 138 330 80 540 72" fill="none" stroke="var(--swoosh)" stroke-width="6" stroke-linecap="round"/>
  </svg>
  <div class="holder">
    <div class="holder-name">Dale Fenwick</div>
    <div class="holder-title">Vice President</div>
  </div>
  <div class="brand">
    <div class="brand-mark"></div>
    <div>
      <div class="brand-name">T.K. Fenwick</div>
      <div class="brand-sub">Manufacturing Company, Inc.</div>
      <div class="brand-since">Since 1918</div>
    </div>
  </div>
  <div class="rule"></div>
  <div class="contacts">
    <div class="contact-col">
      <div class="contact-line"><svg class="icon" viewBox="0 0 12 12"><rect x="1" y="1" width="10" height="10" rx="1" fill="none" stroke="var(--green)" stroke-width="1.4"/></svg>770-555-4821</div>
      <div class="contact-line"><svg class="icon" viewBox="0 0 12 12"><rect x="3" y="0.5" width="6" height="11" rx="1.2" fill="var(--green)"/><rect x="4" y="2" width="4" height="6" fill="#fff"/></svg>770-555-3067</div>
    </div>
    <div class="contact-col">
      <div class="contact-line"><svg class="icon" viewBox="0 0 12 12"><rect x="0.5" y="2" width="11" height="8" fill="var(--green)"/><path d="M1 2.5L6 7L11 2.5" fill="none" stroke="#fff" stroke-width="1"/></svg>dale@tkfenwick.example</div>
      <div class="contact-line"><svg class="icon" viewBox="0 0 12 12"><circle cx="6" cy="6" r="5.2" fill="none" stroke="var(--green)" stroke-width="1.2"/><ellipse cx="6" cy="6" rx="2.2" ry="5.2" fill="none" stroke="var(--green)" stroke-width="1"/><path d="M1 6H11" stroke="var(--green)" stroke-width="1"/></svg>www.tkfenwick.example</div>
    </div>
    <div class="contact-col">
      <div class="contact-line">4700 West Harbor Boulevard</div>
      <div class="contact-line">Suite #150, Roswell, GA 30076</div>
    </div>
  </div>
</section>
<section class="card card-back" aria-label="Card back">
  <div class="back-brand">
    <div class="back-mark"></div>
    <div class="back-name">T.K. Fenwick</div>
  </div>
  <div class="back-web">www.tkfenwick.example</div>
</section>
</body>
</html>
```